Kestrel HVAC Services - High end letter head, Quote Template & Invoice Template

Provide word documents for the below.
- Letterhead for emails & letters.
- Quote template (similar to the attached)
- Invoice template (similar to the attached)
Logo colours should be used.
Modern, bold, professional look.
Kestrel Logo - Vantor Specialist Dealer logo - Contact information

See attachments of previously used documents.

Target Market(s)

High end clients

Industry/Entity Type

Air Conditioning & Mechanical Ventilation (HVAC)

Font styles to use
Sans Serif
Other font styles liked:
• Arial Narrow or similar - Text similar to the KESTREL logo

Requirements
Must have
• Kestrel Logo - Vantor Specialist Dealer logo - Contact information
Nice to have
• Logo colours used throughout the documents
Should not have
• Bright colours, yellow, pink, green etc

```html
<!DOCTYPE html>
<html lang="en">
<head>
<meta charset="utf-8">
<title>Kestrel HVAC Services – Letterhead</title>
<link rel="stylesheet" href="https://fonts.googleapis.com/css2?family=Arimo:wght@400;700&family=Open+Sans:wght@400;600&display=swap">
<style>
  :root {
    --page: #f6f5f3;
    --band: #050505;
    --ink: #3a3a3a;
    --ink-soft: #555555;
    --white: #ffffff;
    --brand-blue: #1a86cc;
    --rule: #8a8a8a;
  }
  * { box-sizing: border-box; margin: 0; padding: 0; }
  html, body { width: 912px; height: 1200px; overflow: hidden; background: var(--page); }
  .letterhead {
    position: relative; width: 912px; height: 1200px;
    background: var(--page); color: var(--ink);
    font-family: "Arimo", Arial, sans-serif;
  }
  .masthead {
    position: absolute; left: 0; top: 0; width: 100%; height: 132px;
    background: var(--band);
  }
  .brand-name {
    position: absolute; left: 70px; top: 46px;
    font-family: "Arimo", Arial, sans-serif; font-weight: 700;
    font-size: 27px; letter-spacing: 0.5px; color: var(--white);
    display: flex; align-items: center; gap: 12px;
  }
  .brand-mark { width: 16px; height: 16px; background: var(--brand-blue); }
  .contact-list {
    position: absolute; left: 612px; top: 41px; list-style: none;
    font-family: "Open Sans", Arial, sans-serif; font-size: 17px;
    color: var(--white); line-height: 22px;
  }
  .contact-list li { display: flex; align-items: center; gap: 8px; }
  .contact-list svg { width: 13px; height: 13px; fill: var(--brand-blue); flex: none; }
  .greeting {
    position: absolute; left: 92px; top: 296px;
    font-size: 24px; font-weight: 400; color: var(--ink);
  }
  .letter-body {
    position: absolute; left: 92px; top: 362px; width: 772px;
    font-size: 13.6px; line-height: 21.5px; color: var(--ink-soft);
    text-align: justify;
  }
  .letter-body p + p { margin-top: 21.5px; }
  .sign-off {
    position: absolute; left: 92px; top: 814px;
    font-size: 13.6px; color: var(--ink-soft);
  }
  .signature {
    position: absolute; left: 92px; top: 842px; width: 112px; height: 46px;
    background: linear-gradient(90deg, rgba(30,30,40,0.10), rgba(30,30,40,0.22), rgba(30,30,40,0.08));
    border-radius: 4px;
  }
  .signatory {
    position: absolute; left: 96px; top: 908px;
    font-size: 18.5px; color: var(--ink);
  }
  .signatory-role {
    position: absolute; left: 96px; top: 934px;
    font-size: 14.5px; color: var(--ink-soft);
  }
  .footer-rule {
    position: absolute; left: 92px; top: 1111px; width: 534px;
    border-top: 1px solid var(--rule);
  }
  .registrations {
    position: absolute; left: 96px; top: 1128px;
    font-family: "Open Sans", Arial, sans-serif; font-size: 13.5px; color: var(--ink-soft);
  }
  .dealer-name {
    position: absolute; left: 648px; top: 1104px; width: 200px;
    font-family: "Arimo", Arial, sans-serif; font-weight: 700;
    font-size: 15px; line-height: 18px; color: var(--brand-blue);
    display: flex; align-items: center; gap: 8px;
  }
  .dealer-mark { width: 14px; height: 14px; background: var(--brand-blue); flex: none; }
</style>
</head>
<body>
<main class="letterhead">
  <header class="masthead">
    <div class="brand-name"><span class="brand-mark"></span>Kestrel HVAC Services</div>
    <ul class="contact-list">
      <li><svg viewBox="0 0 16 16" aria-hidden="true"><path d="M3.5 1l2.3 3.2-1.4 1.6c.9 2 2.4 3.5 4.3 4.4l1.6-1.4L13.5 11 12 14.2C6.5 14 2 9.5 1.8 3z"/></svg>0400 555 019</li>
      <li><svg viewBox="0 0 16 16" aria-hidden="true"><path d="M1 3h14v10H1z M1.5 3.5L8 9l6.5-5.5" /></svg>office@kestrelhvac.com.au</li>
      <li><svg viewBox="0 0 16 16" aria-hidden="true"><path d="M8 1a7 7 0 1 0 0 14A7 7 0 0 0 8 1zm0 1.5c.9 1.2 1.5 2.9 1.6 4.8H6.4C6.5 5.4 7.1 3.7 8 2.5zM2.6 8.7h2.4c.1 1.8.6 3.4 1.3 4.6A5.6 5.6 0 0 1 2.6 8.7zm0-1.4a5.6 5.6 0 0 1 3.7-4.6C5.6 3.9 5.1 5.5 5 7.3zm5.4 6.2c-.9-1.2-1.5-2.9-1.6-4.8h3.2c-.1 1.9-.7 3.6-1.6 4.8zm1.7-.2c.7-1.2 1.2-2.8 1.3-4.6h2.4a5.6 5.6 0 0 1-3.7 4.6zM11 7.3c-.1-1.8-.6-3.4-1.3-4.6a5.6 5.6 0 0 1 3.7 4.6z"/></svg>www.kestrelhvac.com.au</li>
    </ul>
  </header>

  <h1 class="greeting">Dear Mr. Avery,</h1>

  <section class="letter-body">
    <p>Lorem ipsum dolor sit amet, consectetur adipiscing elit. Donec orci purus, luctus vitae dignissim eu, iaculis sed purus. Vivamus faucibus, ipsum nec aliquet viverra, leo mauris condimentum ligula, sit amet sagittis enim ligula quis arcu. Nam egestas tortor id nisi porttitor mattis. In tortor ante, ultricies in suscipit a, tempus non massa. Vivamus et auctor mi. Fusce vel massa nulla. Phasellus nec eros mauris, et scelerisque orci.</p>
    <p>Donec malesuada orci vitae nulla accumsan porta a id massa. Quisque accumsan iaculis magna sit amet fringilla. Maecenas consequat, magna eget tincidunt semper, odio nibh rutrum mi, id feugiat ante nisi eu risus. Vestibulum nunc orci, rhoncus a placerat in, ultricies in mi. Cras mattis varius eros, vel fringilla nisi suscipit eget. Quisque scelerisque sagittis nulla at porttitor.</p>
    <p>Sed id augue vitae urna euismod commodo aliquet a quam. Pellentesque arcu velit, cursus et malesuada ut, consequat et diam. Nullam erat sem, rhoncus id ullamcorper vitae, rhoncus et arcu. In ultricies ultricies nulla, ut rutrum nisi iaculis at. Donec eu magna a metus ornare faucibus. Fusce aliquet faucibus ultricies. Morbi semper, est id tincidunt gravida, sem arcu adipiscing lacus, ac bibendum nulla leo eu purus. Quisque nec diam sed risus consectetur a ccumsan quis quis nibh. Vestibulum id purus lorem.</p>
    <p>It is a long established fact that a reader will be distracted by the readable content of a page when looking at its layout. The point of using Lorem Ipsum is that it has a more-or-less normal distribution of letters, as opposed to using 'Content here, content here', making it look like readable English. Many desktop publishing packages</p>
  </section>

  <p class="sign-off">Sincerely,</p>
  <div class="signature" role="img" aria-label="Handwritten signature of the sender"></div>
  <p class="signatory">James Avery</p>
  <p class="signatory-role">CEO/ Founder</p>

  <footer>
    <div class="footer-rule"></div>
    <p class="registrations">ABN: 55 600 123 478 | Licence No: 512904K | ARC No: AU60217</p>
    <div class="dealer-name"><span class="dealer-mark"></span>Vantor Specialist Dealer</div>
  </footer>
</main>
</body>
</html>
```